Dunfield Inc 1 pg brochure for entrepreneurs

We need a one page brochure (2 sided) designed for a finance and strategy consulting company called Dunfield Inc. which does work in Canada and the United States currently. This company works with entrepreneurs, helping them to establish finance operations, evaluate their financial infomation and apply insight from it to business strategies. Essentially we help entrepreneurs grow their business ... we take care of their finance needs and give them sound business advice ... allowing them to focus on their core business and business strategy.

This one page brochure is meant to caputure what services we provide but also positon that we are also entrepreneurs and we understand how entrepreneurs think .... we not only bring technical competence but cultural insight in this regard as well. We understand how nimble and stealth an entrepreneur's business is so we don't gouge them with expensive consulting fees. We don't want to look like a massive corporation ...we want to look professional, smart and reliable. We want to reflect that we are entrepreneural ourselves even in fact that we have a niche offering that is totally targeted to businesses of this nature.

Major emphasis points for the piece are
1) our core values, this could be a side bar or box
2) the credentials of our founder, he is technically competent and an entrepreneur himself (we have his picture to include)
3) our offerings, what we can do for a company, the client quotes provided are a good illustration of what we offer, the relief we provide a client and of what value we provide - make sure you read these, this could also be a side bar or box, some kind of special call out so the service offerings are very clear

The brochure needs to be editable, so in a format that we can work with it for future, if we need to make updates, one that we can use in Microsoft word and convert to a PDF format. It will be emailed to people (in pdf) and also brought to meetings.

We have a new logo and this design should be an extenstion of it from a colour, look and feel perspective. The piece should also be clean and not too copy heavy so we encourage use of sub-heads, whitespace, etc.

When we send this piece out or hand it to someone, the impression should be "I am comfortable with Dunfield Inc. they can help me and are people who get me, people I can trust to work closely with me on my business who are personally vested in my success".

Hello all, thank you for sumitting designs, there is some great work here.  A few changes/requests ...

Pls add the following headline on the front page right off the top

Entrepreneurs helping entrepreneurs, providing strategic financial services

Can we put Services on the front page? and call them out with treatment in a text box or with something strong that creates emphasis

Can the quote pls be broken up as opposed to one long list of 6 quotes? They can be floated throughout the piece, we can use less of them (or not) and put them on the front and back of the brochure? 

Also looking for the final product to be a little more bold in colour ...

Thx all, let us know if you have questions

Target Market(s)

Individuals (CEO) who runs their own established, yet growing business, who needs a business-minded CFO

Industry/Entity Type

Financial

Requirements
Must have
• Must have photo of founder, include his name and credentials under photo
All copy provide must be included
If not sure of a headline put in dummy text and we will provide headline or sub head copy
Should not have
• Fonts to be clean, no serif fonts. Should compliment logo, not the same font exactly but easily replicable in Microsoft Word and complimentary
No illustrations or cliche clip art

```html
<!DOCTYPE html>
<html lang="en">
<head>
<meta charset="utf-8">
<title>Dunfield Inc – Strategic Financial Services</title>
<link href="https://fonts.googleapis.com/css2?family=Inter:wght@300;400;500;800&display=swap" rel="stylesheet">
<style>
  :root{
    --brand-blue:#0a7ac3;
    --brand-cyan:#2ebfdc;
    --brand-navy:#1e1f5a;
    --tab-notch:#16205a;
    --ink:#3a3a3a;
    --logo-ink:#3a3a20;
    --white:#ffffff;
    --photo-dark:#2a2a2a;
  }
  *{margin:0;padding:0;box-sizing:border-box}
  html,body{width:927px;height:1200px;overflow:hidden;background:var(--white)}
  body{font-family:"Inter",Arial,sans-serif;color:var(--ink);position:relative}
  .page{position:relative;width:927px;height:1200px;overflow:hidden}

  .masthead{position:absolute;left:0;top:0;width:927px;height:166px}
  .brand{position:absolute;left:109px;top:62px;display:flex;align-items:center;gap:14px}
  .brand-mark{width:62px;height:62px;background:var(--brand-blue)}
  .brand-name{font-size:36px;font-weight:500;color:var(--logo-ink);letter-spacing:.5px}
  .website{position:absolute;right:55px;top:125px;font-size:27px;font-weight:300;color:var(--white)}

  .headline{position:absolute;left:68px;top:204px;color:var(--brand-navy);font-weight:300;font-size:63px;line-height:80px;letter-spacing:-.5px}
  .subhead{position:absolute;left:70px;top:366px;color:var(--brand-navy);font-weight:800;font-size:37px;letter-spacing:.2px}

  .intro{position:absolute;left:71px;top:449px;width:770px;font-size:15.6px;line-height:24px;color:var(--ink)}

  .tab{position:absolute;left:73px;width:207px;height:38px;background:var(--brand-blue);color:var(--white);font-size:22px;font-weight:400;padding:5px 0 0 11px}
  .tab::after{content:"";position:absolute;right:0;top:0;border-top:38px solid transparent;border-right:24px solid var(--tab-notch)}
  .tab-about{top:576px}
  .tab-services{top:896px;z-index:2}

  .about{position:absolute;left:73px;top:636px;width:535px;font-size:14px;line-height:22.7px;color:var(--ink)}
  .about p+p{margin-top:22.7px}

  .founder-photo{position:absolute;left:634px;top:589px;width:194px;height:250px;background:radial-gradient(ellipse at 50% 40%,#6b5a4c 0%,#3a3433 45%,var(--photo-dark) 100%);border:1px solid #5a1a1a}
  .founder-name{position:absolute;left:634px;top:851px;font-size:14px;color:#222}
  .founder-title{position:absolute;left:634px;top:872px;font-size:11px;color:#222}

  .services{position:absolute;left:55px;top:910px;width:818px;height:217px;background:var(--brand-cyan)}
  .service-list{position:absolute;top:46px;list-style:none;color:var(--white);font-size:15.6px;line-height:21.5px}
  .service-list li{position:relative;padding-left:21px;margin-bottom:13.5px}
  .service-list li::before{content:"";position:absolute;left:0;top:5px;width:11px;height:11px;background:var(--brand-blue)}
  .col-left{left:28px;width:392px}
  .col-right{left:433px;width:375px}

  .footer{position:absolute;left:0;top:1155px;width:927px;height:45px;background:var(--brand-blue);color:var(--white);font-size:15px;font-weight:300;letter-spacing:-.2px;display:flex;align-items:center;padding-left:24px;white-space:nowrap}
  .footer span{padding:0 8px;flex:none}
  .footer .sep{width:2px;height:26px;background:var(--white);padding:0}
  .footer span:first-child{padding-left:0}
</style>
</head>
<body>
<div class="page">
  <header class="masthead">
    <svg width="927" height="166" viewBox="0 0 927 166" aria-hidden="true">
      <rect width="927" height="166" fill="var(--brand-blue)"/>
      <circle cx="273" cy="58" r="228" fill="var(--brand-cyan)"/>
      <circle cx="273" cy="58" r="216" fill="var(--white)"/>
    </svg>
    <div class="brand">
      <div class="brand-mark"></div>
      <div class="brand-name">Dunfield Inc</div>
    </div>
    <div class="website">www.dunfieldinc.ca</div>
  </header>

  <h1 class="headline">Entrepreneurs helping<br>entrepreneurs,</h1>
  <h2 class="subhead">providing strategic financial services</h2>

  <p class="intro">By engaging Dunfield Inc, entrepreneurs can regularly access senior executive financial acumen and strategic discipline without having to hire a full-time financial executive or overspend on third-party service providers who are transactional in nature.</p>

  <div class="tab tab-about">Who we are?</div>
  <div class="about">
    <p>Dunfield Inc. evolved out of the companies, partnerships and relationships that Martin Kessler, its founder, has nurtured and built over the last 22 years. Mr. Kessler, the founder of Dunfield, is an entrepreneur himself having built his own companies and managed several successful investment funds whose mandates were to invest in entrepreneurial growth companies.</p>
    <p>Over his career, he has worked extensively with entrepreneurs like himself who have struggled to build an experienced and engaged executive management team.</p>
  </div>

  <div class="founder-photo" role="img" aria-label="Portrait photograph of the founder in a dark suit and tie"></div>
  <div class="founder-name">Martin Kessler,</div>
  <div class="founder-title">Founder</div>

  <div class="tab tab-services">Services</div>
  <section class="services">
    <ul class="service-list col-left">
      <li>We work intimately with our clients to determine their corporate and personal objectives</li>
      <li>We evaluate corporate strategies and assist in aligning them with financial ones</li>
      <li>We assist in budgeting, investing, financial forecasting and analysis and asset management</li>
    </ul>
    <ul class="service-list col-right">
      <li>We develop and implement accountability financial systems, processes and reporting</li>
      <li>We manage capital raising efforts, tax structuring issues and corporate transactions including mergers, acquisitions, and the sale of your business</li>
    </ul>
  </section>

  <footer class="footer">
    <span>2150 8 Street SW, Calgary Alberta, Canada, T2T 3K1</span>
    <span class="sep"></span>
    <span>P 403.555.0148</span>
    <span class="sep"></span>
    <span>F 000 000 000</span>
    <span class="sep"></span>
    <span>E martink@dunfieldinc.ca</span>
  </footer>
</div>
</body>
</html>
```